Systems and Technology Consultants - Website

Design & Build a website for a new company which operates in the Systems and Technology space for Transportation, Government and Commercial sectors.

Overall design should be minimalist in nature.
Should also have a feed that provides news and event updates on the main page.
Logo has already been awarded and should be incorporated into the site.

We like the overall layout, functionality and simplicity of the below sites. Submitted designs could be similar to or a combination of the aspects on these sites, or perhaps a whole different concept - we are open to new ideas.
Norvique.com
Teblo.it

Update 1 Dated 27 May 2014

All I am moving away from the Teblo.it website and would like it to be more aligned with Norvique.com not only in layout but in functionality. I will be extending the deadline of this design brief for two weeks to incorporate additional requirements and will add addtional funding to the project.

Apologies for not having more information available to provide but with so many submissions its getting confusing.

Thanks Derek

Please note that the brief has been updated and the deadline has been extended.

Important: We will need two language versions of the website, English and Arabic; the website is hosted on HostPelican

Hello All, Thank you for your submissions. We have narrowed it down to the final 6 designers and I just wanted to take a moment and provide a bit of feedback regarding the concepts that we like and the modifications we are looking for. First, let me mention some of the design functions we like. - At the top of the homepage we really like the "region" or "language" tab so that the website can be viewed in both English and Arabic. - We like the homepage to have clear color variation so that the different sections of the homepage are distinct. Additionally, we like the bottom portion of the homepage to be in red. We feel that draws attention to our contact information. Again, we would like the colors to integrate black, gray-scale, red, etc. - Having a search tab at the top of the home page, or integrated into the main image, so that the site is easy to navigate. - We especially like the main image to have the scrolling tabs at the bottom so it is easy to browse the services offered (Consultancy, Solutions Architecture, Masters Systems Integration, Independent Design Review). - In regards to the services offered tab we really like the idea that a few people presented that have the outside of our logo with an icon in the middle of consultancy, solutions, etc., etc. Secondly, as mentioned in our brief we really enjoy the design of norvique site. Specially, we enjoy the strong iconic images they use, the way the tabs at the top scroll easily, and contact us page that generates an email. Lastly, I've included some photos of the concept we have been working on. What we are trying to demonstrate is how our company offers a range of services that are essentially linked together. We provide individual services that when combined present the full service package. We would like this concept to be integrated into the over concept of our website. Please feel free to ask for clarification of any of the above points or contact us if you have any additional questions. We appreciate all of your hard work and are very excited to see the updated designs. Best, Marta Vennick Quelbrant Senior Program Manager marta.vennick@quelbrant-example.com

Industry/Entity Type

Government

Font styles to use
Serif
Sans Serif

Requirements
Must have
• Must work on/adapt to various/mobile devices (responsive)
Must be simple and straightforward
Colors should be in line/matching with logo
2 language versions: English and Arabic (no Thai)
Services should be the first group/row of items after/below the main image
Note: the website will be hosted by hostpelican
Nice to have
• Submit feedback form
What's New section
The banner at the bottom of the site should not be too large; we would like a narrow one more
It would be nice if the header/top banner (with Home, About, etc. tabs) could stay in place as you scroll down (like Norvique and Chatterloop)
We will likely only use one image with a Company slogan on the Home page rather than a carousel of images to rotate through
Should not have
• This is the existing website: http://www.quelbrant-example.org
We do not like the animation, the way the banner icons/titles bounce
Not simple enough, we don't like the functionality or how pages load so slowly
We do not like the logo centered - it should be at the left
The banner and its tabs should not be towards the right, we would like them to be centered, to go all the way across and to be below the logo

```html
<!DOCTYPE html>
<html lang="en">
<head>
<meta charset="utf-8">
<title>Quelbrant — Systems Professionals</title>
<link rel="stylesheet" href="https://fonts.googleapis.com/css2?family=Open+Sans:ital,wght@0,400;0,600;1,400&family=Source+Sans+3:wght@400;600&family=Arimo:wght@400&display=swap">
<style>
:root{
  --red:#e8414b;
  --red-soft:#f2606a;
  --ink:#222;
  --text:#555;
  --muted:#888;
  --top-bar:#1f1f1f;
  --section-grey:#ebebeb;
  --footer:#464646;
  --footer-rule:#8a8a8a;
  --bottom-bar:#1c1c1c;
  --quote-blue:#2a86c8;
  --white:#fff;
}
*{box-sizing:border-box;margin:0;padding:0}
html,body{width:735px;height:1200px;overflow:hidden;background:var(--white)}
body{position:relative;font-family:"Source Sans 3",sans-serif;color:var(--text)}
.abs{position:absolute}

.top-bar{left:0;top:0;width:735px;height:18px;background:var(--top-bar)}
.site-header{left:0;top:18px;width:735px;height:82px;background:var(--white)}
.brand{left:105px;top:30px;display:flex;align-items:center;gap:7px}
.brand-mark{width:14px;height:14px;background:var(--red)}
.brand-name{font-family:"Source Sans 3",sans-serif;font-weight:600;font-size:17px;letter-spacing:1.5px;color:var(--red)}
.main-nav{left:294px;top:36px;display:flex;align-items:center;font-family:"Open Sans",sans-serif;font-size:8.6px;color:var(--ink)}
.main-nav a{color:inherit;text-decoration:none;padding:0 7.5px;line-height:18px}
.main-nav a.active{background:var(--red);color:var(--white);padding:0 8px;margin-right:0}

.hero{left:0;top:100px;width:735px;height:365px;background:linear-gradient(100deg,#e3e8ec 0%,#d6dde3 40%,#c9d4dd 60%,#b9c7d3 100%)}
.hero-title{left:103px;top:217px;font-family:"Open Sans",sans-serif;font-size:19px;color:var(--ink);letter-spacing:.2px}
.hero-sub{left:106px;top:250px;font-family:"Open Sans",sans-serif;font-size:12.5px;color:#333}
.slider-ctrl{left:107px;top:282px;width:95px;height:16px;border:1px solid #9aa3ab;border-radius:2px;background:rgba(255,255,255,.85)}

.services{left:0;top:465px;width:735px;height:177px;background:var(--section-grey)}
.section-title{font-family:"Source Sans 3",sans-serif;font-weight:600;font-size:12px;color:var(--red)}
.services .section-title{left:0;width:735px;top:16px;text-align:center}
.services-lead{left:0;width:735px;top:35px;text-align:center;font-size:9px;color:#666}
.service{top:57px;width:110px;text-align:center}
.service-badge{width:66px;height:66px;border-radius:50%;background:var(--white);margin:0 auto;box-shadow:0 2px 4px rgba(0,0,0,.18);display:flex;align-items:center;justify-content:center}
.service-name{margin-top:12px;font-family:"Source Sans 3",sans-serif;font-weight:600;font-size:11px;color:#333;letter-spacing:.2px}

.vision-photo{left:105px;top:661px;width:213px;height:121px;background:linear-gradient(90deg,#3b6a9b 0%,#7ea5c9 45%,#b8c2c6 75%,#8e9aa1 100%)}
.vision .section-title{left:331px;top:658px}
.vision-text{left:331px;top:677px;width:298px;font-size:8.4px;line-height:14.6px;color:#666;text-align:justify}
.btn-more{left:330px;top:758px;width:80px;height:23px;background:var(--red-soft);color:var(--white);font-family:"Open Sans",sans-serif;font-size:10px;line-height:23px;text-align:center;border-radius:2px}

.news-heading{left:105px;top:806px;font-family:"Open Sans",sans-serif;font-size:14px;color:var(--ink)}
.news-item{top:832px;width:122px}
.news-photo{width:122px;height:74px}
.news-meta{position:relative;height:40px;margin-top:10px}
.news-date{position:absolute;left:0;top:0}
.news-title{position:absolute;left:36px;top:-2px;font-family:"Source Sans 3",sans-serif;font-size:10.5px;color:var(--red)}
.news-text{position:absolute;left:36px;top:13px;width:90px;font-size:7px;line-height:10px;color:#888}

.testimonial{left:0;top:968px;width:735px;height:106px;background:linear-gradient(180deg,#fff 0%,#ececec 100%)}
.avatar{left:128px;top:35px;width:60px;height:60px;border-radius:50%;background:radial-gradient(circle at 50% 45%,#e8cdb5 0%,#d9b996 55%,#b88f66 100%);box-shadow:0 1px 3px rgba(0,0,0,.25)}
.quote-mark{font-family:Georgia,serif;font-weight:700;font-size:34px;color:var(--quote-blue);line-height:1}
.quote-open{left:205px;top:33px}
.quote-close{left:567px;top:70px}
.quote-text{left:239px;top:39px;width:350px;font-size:8.6px;line-height:13px;color:#444}
.quote-author{left:239px;top:80px;font-family:"Open Sans",sans-serif;font-style:italic;font-size:8px;color:var(--quote-blue)}

.site-footer{left:0;top:1074px;width:735px;height:86px;background:var(--footer);font-family:"Arimo",sans-serif;color:#eee;letter-spacing:.6px}
.footer-rule{left:105px;top:33px;width:435px;height:1px;background:var(--footer-rule)}
.footer-col{top:20px}
.footer-col h4{font-weight:400;font-size:8px;color:#f2f2f2;margin-bottom:16px;letter-spacing:.9px}
.footer-col p{font-size:8px;line-height:11.6px;color:#e8e8e8}
.social{left:567px;top:20px;display:flex;gap:6px}
.social span{width:16px;height:16px;border-radius:2px}
.phone{left:559px;top:45px;font-size:7.5px;color:#eee}

.bottom-bar{left:0;top:1160px;width:735px;height:40px;background:var(--bottom-bar);color:#f0f0f0;font-family:"Arimo",sans-serif;font-size:7px;text-align:center;line-height:40px}
</style>
</head>
<body>

<div class="abs top-bar"></div>

<header class="abs site-header">
  <div class="abs brand" style="top:20px">
    <span class="brand-mark"></span>
    <span class="brand-name">QUELBRANT</span>
  </div>
  <nav class="abs main-nav">
    <a class="active">HOME</a>
    <a>BUSINESS UNITS</a>
    <a>SERVICES</a>
    <a>ABOUT US</a>
    <a>LOCATIONS</a>
    <a>CONTACT US</a>
  </nav>
</header>

<section class="abs hero" role="img" aria-label="Smiling engineer in a white hard hat reading a tablet, with construction workers and machinery blurred behind him"></section>
<h1 class="abs hero-title">SYSTEMS PROFESSIONALS</h1>
<p class="abs hero-sub">CONSTRUCTION</p>
<div class="abs slider-ctrl">
  <svg width="95" height="16" viewBox="0 0 95 16">
    <path d="M11 5 L8 8 L11 11" fill="none" stroke="#222" stroke-width="1.4"/>
    <path d="M18 5 L21 8 L18 11" fill="none" stroke="#888" stroke-width="1.2"/>
    <line x1="28" y1="1" x2="28" y2="15" stroke="#b5bcc2"/>
    <circle cx="36" cy="8" r="2" fill="#a9b0b6"/>
    <circle cx="46" cy="8" r="2" fill="#a9b0b6"/>
    <circle cx="56" cy="8" r="2.2" fill="#222"/>
    <circle cx="66" cy="8" r="2" fill="#a9b0b6"/>
    <circle cx="76" cy="8" r="2" fill="#a9b0b6"/>
    <circle cx="86" cy="8" r="2" fill="#a9b0b6"/>
  </svg>
</div>

<section class="abs services">
  <h2 class="abs section-title">SEVICES OFFERED</h2>
  <p class="abs services-lead">Lorem Ipsum is simply dummy text of the printing and typesetting industry</p>

  <div class="abs service" style="left:97px">
    <div class="service-badge">
      <svg width="34" height="30" viewBox="0 0 34 30" fill="#e8414b">
        <circle cx="7" cy="16" r="3.5"/><path d="M1 29 a6 6 0 0 1 12 0 z"/>
        <circle cx="25" cy="6" r="3.5" fill="none" stroke="#e8414b" stroke-width="1.5"/>
        <path d="M19 18 a6 6 0 0 1 12 0 z" fill="none" stroke="#e8414b" stroke-width="1.5"/>
        <path d="M11 10 L17 4 M14 4 L17 4 L17 7" fill="none" stroke="#e8414b" stroke-width="1.5"/>
        <path d="M22 20 L16 26 M16 23 L16 26 L19 26" fill="none" stroke="#e8414b" stroke-width="1.5"/>
      </svg>
    </div>
    <p class="service-name">CONSULTING</p>
  </div>

  <div class="abs service" style="left:205px">
    <div class="service-badge">
      <svg width="26" height="32" viewBox="0 0 26 32" fill="#e8414b">
        <path d="M5 9 a8 8 0 0 1 16 0 h2 v2 H3 v-2 z"/>
        <circle cx="13" cy="13" r="5"/>
        <path d="M2 32 v-7 a7 7 0 0 1 7 -7 h8 a7 7 0 0 1 7 7 v7 z"/>
        <rect x="12" y="21" width="2" height="8" fill="#fff"/>
      </svg>
    </div>
    <p class="service-name">ENGINEERING</p>
  </div>

  <div class="abs service" style="left:313px">
    <div class="service-badge">
      <svg width="34" height="30" viewBox="0 0 34 30" fill="#e8414b">
        <circle cx="9" cy="5" r="3.5"/>
        <path d="M5 10 h8 l2 9 h-3 l-1 -5 -1 15 h-3 l-1 -9 -2 9 h-3 z"/>
        <path d="M15 15 L27 27" stroke="#e8414b" stroke-width="1.5"/>
        <path d="M20 29 L26 19 L33 29 z"/>
      </svg>
    </div>
    <p class="service-name">CONSTRUCTION</p>
  </div>

  <div class="abs service" style="left:417px">
    <div class="service-badge">
      <svg width="32" height="32" viewBox="0 0 32 32" fill="#e8414b">
        <path d="M6 3 L29 26 L26 29 L3 6 z"/>
        <path d="M26 2 a6 6 0 0 0 -6 8 L4 26 L6 28 L22 12 a6 6 0 0 0 8 -6 l-4 2 -2 -2 2 -4 z"/>
      </svg>
    </div>
    <p class="service-name">OPERATIONS</p>
  </div>

  <div class="abs service" style="left:523px">
    <div class="service-badge">
      <svg width="34" height="28" viewBox="0 0 34 28" fill="#e8414b">
        <circle cx="22" cy="7" r="6"/>
        <path d="M12 27 v-5 a9 9 0 0 1 9 -8 h2 a9 9 0 0 1 9 8 v5 z"/>
        <circle cx="11" cy="9" r="5.5"/>
        <path d="M1 28 v-4 a8 8 0 0 1 8 -7 h4 a8 8 0 0 1 8 7 v4 z"/>
      </svg>
    </div>
    <p class="service-name">MAINTENANCE</p>
  </div>
</section>

<section class="vision">
  <div class="abs vision-photo" role="img" aria-label="Worker in a denim shirt holding a yellow hard hat in front of a building wrapped in scaffolding"></div>
  <h2 class="abs section-title">QUELBRANT - OUR VISION</h2>
  <p class="abs vision-text">quelbrant specializes in delivering quality professional services and technical projects that support larger business goals. &nbsp;systems are tools that support a greater business function and need. we understand that most technical projects are conceptualized to support a larger vision with actual business goals in mind aprofessional services to meet those goals.</p>
  <div class="abs btn-more">READ MORE</div>
</section>

<section class="news">
  <h2 class="abs news-heading">NEWS &amp; EVENTS</h2>

  <article class="abs news-item" style="left:105px">
    <div class="news-photo" role="img" aria-label="Concrete building under construction with a tower crane" style="background:linear-gradient(180deg,#8fb4d6 0%,#a9b3b8 45%,#8a857c 100%)"></div>
    <div class="news-meta">
      <svg class="news-date" width="28" height="36" viewBox="0 0 28 36">
        <rect x="0" y="4" width="28" height="32" fill="#d4d4d4"/>
        <rect x="5" y="0" width="3" height="8" fill="#bdbdbd"/><rect x="20" y="0" width="3" height="8" fill="#bdbdbd"/>
        <rect x="4" y="15" width="20" height="16" fill="#fff"/>
        <text x="14" y="27" text-anchor="middle" font-family="Arimo,sans-serif" font-size="9" fill="#222">12</text>
      </svg>
      <p class="news-title">PELENTE MOR.</p>
      <p class="news-text">Lorem ipsum dolor sit amt consetes ctetur adipiscin.</p>
    </div>
  </article>

  <article class="abs news-item" style="left:238px">
    <div class="news-photo" role="img" aria-label="Worker's hands holding a red hard hat beside a tool belt" style="background:linear-gradient(135deg,#9fb0b8 0%,#c9b48a 50%,#b23a34 75%,#6d7f8a 100%)"></div>
    <div class="news-meta">
      <svg class="news-date" width="28" height="36" viewBox="0 0 28 36">
        <rect x="0" y="4" width="28" height="32" fill="#d4d4d4"/>
        <rect x="5" y="0" width="3" height="8" fill="#bdbdbd"/><rect x="20" y="0" width="3" height="8" fill="#bdbdbd"/>
        <rect x="4" y="15" width="20" height="16" fill="#fff"/>
        <text x="14" y="27" text-anchor="middle" font-family="Arimo,sans-serif" font-size="9" fill="#222">13</text>
      </svg>
      <p class="news-title">PELENTE MOR.</p>
      <p class="news-text">Lorem ipsum dolor sit amt consetes ctetur adipiscin.</p>
    </div>
  </article>

  <article class="abs news-item" style="left:372px">
    <div class="news-photo" role="img" aria-label="Tower cranes against a blue sky with white clouds" style="background:linear-gradient(180deg,#2f5fae 0%,#6f93cf 45%,#dfe6ef 75%,#7c8590 100%)"></div>
    <div class="news-meta">
      <svg class="news-date" width="28" height="36" viewBox="0 0 28 36">
        <rect x="0" y="4" width="28" height="32" fill="#d4d4d4"/>
        <rect x="5" y="0" width="3" height="8" fill="#bdbdbd"/><rect x="20" y="0" width="3" height="8" fill="#bdbdbd"/>
        <rect x="4" y="15" width="20" height="16" fill="#fff"/>
        <text x="14" y="27" text-anchor="middle" font-family="Arimo,sans-serif" font-size="9" fill="#222">14</text>
      </svg>
      <p class="news-title">PELENTE MOR.</p>
      <p class="news-text">Lorem ipsum dolor sit amt consetes ctetur adipiscin.</p>
    </div>
  </article>

  <article class="abs news-item" style="left:505px">
    <div class="news-photo" role="img" aria-label="Engineer in an orange hard hat reviewing plans at a building site" style="background:linear-gradient(180deg,#3f6fb8 0%,#8eaad3 45%,#c8c6c0 70%,#2b2d33 100%)"></div>
    <div class="news-meta">
      <svg class="news-date" width="28" height="36" viewBox="0 0 28 36">
        <rect x="0" y="4" width="28" height="32" fill="#d4d4d4"/>
        <rect x="5" y="0" width="3" height="8" fill="#bdbdbd"/><rect x="20" y="0" width="3" height="8" fill="#bdbdbd"/>
        <rect x="4" y="15" width="20" height="16" fill="#fff"/>
        <text x="14" y="27" text-anchor="middle" font-family="Arimo,sans-serif" font-size="9" fill="#222">15</text>
      </svg>
      <p class="news-title">PELENTE MOR.</p>
      <p class="news-text">Lorem ipsum dolor sit amt consetes ctetur adipiscin.</p>
    </div>
  </article>
</section>

<section class="abs testimonial">
  <div class="abs avatar" role="img" aria-label="Portrait photo of the client giving the testimonial"></div>
  <span class="abs quote-mark quote-open">&ldquo;</span>
  <p class="abs quote-text">Vis id minim dicant sensibus. Pri aliquip conclusionemque ad, ad malis evertitur torquatos his. Has ei solum harum reprimique, id illum saperet tractatos his. Ei omnis soleat antiopam quo. Ad augue inani postulant mel, mel ea qualisque forensibus.</p>
  <span class="abs quote-mark quote-close">&rdquo;</span>
  <p class="abs quote-author">Jane Doe</p>
</section>

<footer class="abs site-footer">
  <div class="abs footer-rule"></div>
  <div class="abs footer-col" style="left:109px">
    <h4>COMPANY</h4>
    <p>About Us<br>News<br>Join us</p>
  </div>
  <div class="abs footer-col" style="left:211px">
    <h4>CUSTOMERS</h4>
    <p>Game<br>Finance<br>Others</p>
  </div>
  <div class="abs footer-col" style="left:322px">
    <h4>SUPPORT</h4>
    <p>Contact Us<br>On-line Service</p>
  </div>
  <div class="abs footer-col" style="left:426px">
    <h4>CONTACT US</h4>
    <p>address: 14 harrowgate lane,<br>unit 7, eastvale 40912</p>
  </div>
  <div class="abs social" aria-label="Social links">
    <span style="background:#6f96b8"></span>
    <span style="background:#4a6ea3"></span>
    <span style="background:#5fb3d6"></span>
  </div>
  <p class="abs phone">PH : 5021 3370 64</p>
</footer>

<div class="abs bottom-bar">Copyright © 2014. All rights reserved.</div>

</body>
</html>
```